Volbrey Inc Business Card

Looking to get an updated business card for a Contract Machining company (www.volbreyinc.example) - looking for a clean design the portrays the technical nature of the business - colors can follow the website design and be in any combination that makes sense (red black, white, metallic or silver) - logos attached for use also. Would like space for: Name, title, business phone (555 214-3086), cell phone , website (www.volbreyinc.example) - possibly QR code could be integrated for website (designer choice), business address - 418 Harlow Bend, Corwin Falls, NV 48199 (cards will be for 4 employees, I will either need to modify a template or I can provide individual information)
Target Market(s)
Aerospace, defense and medical device manufacturing companies that need machining
Industry/Entity Type
Machining for aerospace, defense, medical
Contact Information for Business Card
Name, Title, Business Phone, Cell Phone, email, business website and business address
Look and feel

```html
<!DOCTYPE html>
<html lang="en">
<head>
<meta charset="utf-8">
<title>Volbrey Inc Business Card</title>
<link href="https://fonts.googleapis.com/css2?family=Montserrat:wght@400;600;800&display=swap" rel="stylesheet">
<style>
  :root {
    --brand-red: #b01e24;
    --paper: #ffffff;
    --ink: #2b2b2b;
    --muted: #7a7a7a;
    --backdrop: #3d3d3d;
  }
  * { box-sizing: border-box; margin: 0; padding: 0; }
  html, body { width: 1200px; height: 803px; overflow: hidden; }
  body {
    background: var(--backdrop);
    font-family: "Montserrat", Arial, sans-serif;
    display: flex;
    align-items: center;
    justify-content: center;
    gap: 44px;
  }
  .card {
    width: 520px;
    height: 298px;
    border-radius: 18px;
    position: relative;
    overflow: hidden;
  }
  .card-front { background: var(--paper); }
  .card-back {
    background: var(--brand-red);
    display: flex;
    flex-direction: column;
    align-items: center;
    justify-content: center;
    gap: 16px;
  }
  .front-info {
    position: absolute;
    left: 30px;
    top: 34px;
    width: 250px;
  }
  .wordmark {
    font-weight: 800;
    color: var(--brand-red);
    font-size: 26px;
    letter-spacing: 0.5px;
    line-height: 1;
    white-space: nowrap;
  }
  .person-name {
    margin-top: 26px;
    font-weight: 800;
    color: var(--brand-red);
    font-size: 17px;
  }
  .person-title {
    color: var(--muted);
    font-size: 11px;
    margin-top: 2px;
  }
  .address {
    margin-top: 14px;
    color: var(--ink);
    font-size: 11.5px;
    line-height: 1.35;
  }
  .contact-list {
    list-style: none;
    margin-top: 12px;
    color: var(--ink);
    font-size: 11.5px;
    line-height: 1.5;
  }
  .contact-list li { display: flex; align-items: center; gap: 7px; }
  .contact-icon { width: 10px; height: 10px; flex: none; }
  .front-emblem {
    position: absolute;
    right: 26px;
    top: 24px;
    width: 250px;
    height: 250px;
    border-radius: 50%;
    background: var(--brand-red);
  }
  .back-emblem {
    width: 150px;
    height: 150px;
    border-radius: 50%;
    background: var(--paper);
  }
  .wordmark-reversed { color: var(--paper); font-size: 30px; }
</style>
</head>
<body>
  <section class="card card-front" aria-label="Business card front">
    <div class="front-info">
      <div class="wordmark">VOLBREY INC.</div>
      <div class="person-name">Dana Whitlow</div>
      <div class="person-title">President</div>
      <div class="address">418 Harlow Bend<br>Corwin Falls, NV 48199</div>
      <ul class="contact-list">
        <li>
          <svg class="contact-icon" viewBox="0 0 10 10"><path d="M2 1 L4 1 L4.5 3 L3.3 3.8 Q4.2 5.8 6.2 6.7 L7 5.5 L9 6 L9 8 Q9 9 8 9 Q1 8.5 1 2 Q1 1 2 1 Z" fill="var(--brand-red)"/></svg>
          555 214-3086
        </li>
        <li>
          <svg class="contact-icon" viewBox="0 0 10 10"><rect x="2.5" y="0.8" width="5" height="8.4" rx="1" fill="none" stroke="var(--brand-red)" stroke-width="1.2"/></svg>
          555 730-4821
        </li>
        <li>
          <svg class="contact-icon" viewBox="0 0 10 10"><rect x="0.8" y="2" width="8.4" height="6" fill="var(--brand-red)"/><path d="M0.8 2 L5 5.5 L9.2 2" fill="none" stroke="#fff" stroke-width="0.9"/></svg>
          info@volbreyinc.example
        </li>
        <li>
          <svg class="contact-icon" viewBox="0 0 10 10"><circle cx="5" cy="5" r="4.3" fill="var(--brand-red)"/><path d="M0.7 5 H9.3 M5 0.7 Q2.5 5 5 9.3 M5 0.7 Q7.5 5 5 9.3" fill="none" stroke="#fff" stroke-width="0.7"/></svg>
          www.volbreyinc.example
        </li>
      </ul>
    </div>
    <div class="front-emblem" aria-hidden="true"></div>
  </section>

  <section class="card card-back" aria-label="Business card back">
    <div class="back-emblem" aria-hidden="true"></div>
    <div class="wordmark wordmark-reversed">VOLBREY INC.</div>
  </section>
</body>
</html>
```